Business card for my new company (Accounting firm)

I need a business card for my new business Brightwell Advisory and Ledger SA. Our services are accounting, tax, audit and financial management. Our customers are small companies, start-ups and new companies. The final design has to show financial security, trust and growth. Please find our logo attached to the business card. Text for the business card: Brightwell Advisory and Ledger SA Tomas Varenholt Director and Founder Certified Accountant Tel. 022 418 57 34 tv@clairevalconseil.ch www.clairevalconseil.ch Rue des Vergières 27 1201 Geneva
Target Market(s)
Our customers are small companies, start-ups and new companies.
Industry/Entity Type
Finance And Accounting
Contact Information for Business Card
Claireval Conseil et Comptes SA
Tomas Varenholt
Directeur et Fondateur
Expert-comptable diplômé
Tél. 022 418 57 34
tv@clairevalconseil.ch
www.clairevalconseil.ch
Rue des Vergières 27
1201 Genève

```html
<!DOCTYPE html>
<html lang="fr">
<head>
<meta charset="utf-8">
<title>Claireval Conseil et Comptes SA – carte de visite</title>
<link href="https://fonts.googleapis.com/css2?family=Lato:wght@400;700&display=swap" rel="stylesheet">
<style>
  :root {
    --page: #3a3a3c;
    --card: #2b2b2c;
    --card-pattern-a: #2f2f30;
    --card-pattern-b: #262627;
    --blue: #1f8fd6;
    --blue-deep: #1d6fb0;
    --text: #f2f2f2;
  }
  * { box-sizing: border-box; margin: 0; padding: 0; }
  html, body { width: 1200px; height: 900px; overflow: hidden; }
  body {
    background: var(--page);
    font-family: "Lato", sans-serif;
    display: flex;
    flex-direction: column;
    align-items: center;
    justify-content: center;
    gap: 40px;
  }
  .card {
    width: 700px;
    height: 400px;
    background: var(--card);
    border-radius: 4px;
    box-shadow: 0 10px 30px rgba(0,0,0,.45);
    position: relative;
    overflow: hidden;
  }
  /* front */
  .card-front { display: flex; align-items: center; }
  .brand {
    width: 300px;
    display: flex;
    align-items: center;
    justify-content: center;
    gap: 14px;
  }
  .brand-square { width: 26px; height: 26px; background: var(--blue); }
  .brand-name {
    color: var(--text);
    font-weight: 700;
    font-size: 40px;
    letter-spacing: 2px;
  }
  .divider {
    width: 2px;
    height: 260px;
    background: var(--blue-deep);
  }
  .details { padding-left: 40px; color: var(--text); }
  .person-name {
    color: var(--blue);
    font-weight: 700;
    font-size: 30px;
    margin-bottom: 6px;
  }
  .person-role, .address-line { font-size: 17px; line-height: 1.35; }
  .address { margin-top: 10px; }
  .contact { list-style: none; margin-top: 14px; }
  .contact li {
    display: flex; align-items: center; gap: 10px;
    font-size: 17px; line-height: 1.4;
  }
  .contact svg { width: 14px; height: 14px; fill: var(--blue); flex: none; }
  /* back */
  .card-back {
    background: linear-gradient(135deg, var(--card-pattern-a), var(--card-pattern-b));
    display: flex; align-items: center; justify-content: center;
  }
  .back-brand { display: flex; align-items: center; gap: 10px; }
  .back-brand .brand-square { width: 18px; height: 18px; }
  .back-brand .brand-name { color: var(--blue); font-size: 24px; }
</style>
</head>
<body>
  <section class="card card-front">
    <div class="brand">
      <span class="brand-square"></span>
      <span class="brand-name">CLAIREVAL</span>
    </div>
    <div class="divider"></div>
    <div class="details">
      <p class="person-name">Tomas Varenholt</p>
      <p class="person-role">Directeur et Fondateur</p>
      <p class="person-role">Expert-comptable diplômé</p>
      <div class="address">
        <p class="address-line">Claireval Conseil et Comptes SA</p>
        <p class="address-line">Rue des Vergières 27</p>
        <p class="address-line">1201 Genève</p>
      </div>
      <ul class="contact">
        <li>
          <svg viewBox="0 0 16 16" aria-hidden="true"><path d="M3.5 1l3 3-1.6 1.8c.9 2 2.3 3.4 4.3 4.3L11 8.5l3 3-2 2.5C6.5 13.5 2.5 9.5 1 4z"/></svg>
          022 418 57 34
        </li>
        <li>
          <svg viewBox="0 0 16 16" aria-hidden="true"><path d="M1 3h14v10H1z M1.5 3.5L8 9l6.5-5.5" stroke="#2b2b2c" stroke-width="1.2"/></svg>
          tv@clairevalconseil.ch
        </li>
        <li>
          <svg viewBox="0 0 16 16" aria-hidden="true"><circle cx="8" cy="8" r="7"/><path d="M1 8h14M8 1c-3 3.5-3 10.5 0 14M8 1c3 3.5 3 10.5 0 14" stroke="#2b2b2c" stroke-width="1" fill="none"/></svg>
          www.clairevalconseil.ch
        </li>
      </ul>
    </div>
  </section>

  <section class="card card-back" role="img" aria-label="Motif répété discret de la marque sur fond anthracite">
    <div class="back-brand">
      <span class="brand-square"></span>
      <span class="brand-name">CLAIREVAL</span>
    </div>
  </section>
</body>
</html>
```